Card Design for my dog training business Brightpaw Obedience

Need a business card design for my dog training business with my new logo. Want the card to come off professional yet fun. Want it to be very eye catchy as well. I normally have these at vet clinics, pet stores, and groomers. so need it to look better than my competitors.
Target Market(s)
dog owners
Industry/Entity Type
Dog Training
Contact Information for Business Card
needs logo, my name and info
Font styles to use
Serif
Colors
0255a3
ffffff
ec1f27
000000
333333
fbfbfb
Requirements
Must have
- Brightpaw Obedience
- Felix Orland
- 415 903 2276
- info@brightpawobedience.example
- www.brightpawobedience.example

```html
<!DOCTYPE html>
<html lang="en">
<head>
<meta charset="utf-8">
<title>Brightpaw Obedience — Business Card</title>
<link rel="stylesheet" href="https://fonts.googleapis.com/css2?family=EB+Garamond:ital,wght@0,500;1,400&family=Open+Sans:wght@400;700&display=swap">
<style>
  :root {
    --stage: #2b2b2b;
    --card: #ffffff;
    --ink: #000000;
    --ink-soft: #333333;
    --band: #1c1c1c;
    --paper-tint: #fbfbfb;
    --on-dark: #ffffff;
    --art-light: #f2f2f2;
    --art-dark: #8a8a8a;
  }
  * { margin: 0; padding: 0; box-sizing: border-box; }
  html, body { width: 1200px; height: 959px; overflow: hidden; }
  body { background: var(--stage); position: relative; font-family: "Open Sans", Arial, sans-serif; }

  .card { position: absolute; background: var(--card); overflow: hidden; }

  /* Front: landscape */
  .card--front { left: 70px; top: 300px; width: 620px; height: 354px; }
  .front-brand {
    position: absolute; left: 0; right: 0; top: 120px;
    display: flex; align-items: center; justify-content: center; gap: 12px;
  }
  .brand-mark { width: 18px; height: 18px; background: var(--ink); }
  .brand-name {
    font-family: "EB Garamond", Georgia, serif; font-weight: 500;
    font-size: 36px; letter-spacing: 1px; color: var(--ink); text-transform: uppercase;
  }
  .front-tagline {
    position: absolute; left: 0; right: 0; top: 210px; text-align: center;
    font-family: "EB Garamond", Georgia, serif; font-style: italic;
    font-size: 21px; color: var(--ink-soft);
  }

  /* Back: portrait */
  .card--back { left: 770px; top: 160px; width: 360px; height: 630px; }
  .back-brand {
    position: absolute; left: 0; right: 0; top: 40px; text-align: center;
    border-top: 2px solid var(--ink); border-bottom: 2px solid var(--ink);
    margin: 0 40px; padding: 10px 0;
  }
  .back-brand .brand-name { font-size: 27px; }
  .contact-band {
    position: absolute; left: 0; right: 0; bottom: 0; height: 300px;
    background: var(--band);
  }
  .illustration {
    position: absolute; left: 40px; top: 150px; width: 290px; height: 250px;
    background: linear-gradient(160deg, var(--art-light), var(--art-dark));
    border: 3px solid var(--ink);
  }
  .contact {
    position: absolute; left: 40px; right: 20px; top: 440px; color: var(--on-dark);
  }
  .contact-name { font-weight: 700; font-size: 23px; margin-bottom: 14px; }
  .contact-line {
    display: flex; align-items: center; gap: 9px;
    font-size: 14.5px; line-height: 1.75;
  }
  .contact-line svg { width: 14px; height: 14px; flex: none; fill: var(--on-dark); }
</style>
</head>
<body>

  <section class="card card--front" aria-label="Business card front">
    <div class="front-brand">
      <span class="brand-mark"></span>
      <span class="brand-name">Brightpaw Obedience</span>
    </div>
    <p class="front-tagline">“Training dogs across Texas one dog at a time.”</p>
  </section>

  <section class="card card--back" aria-label="Business card back">
    <div class="back-brand"><span class="brand-name">Brightpaw Obedience</span></div>
    <div class="contact-band"></div>
    <div class="illustration" role="img" aria-label="Black and white illustration of two dogs over a Texas state outline"></div>
    <div class="contact">
      <p class="contact-name">Felix Orland</p>
      <p class="contact-line">
        <svg viewBox="0 0 16 16" aria-hidden="true"><path d="M3 1h3l1.5 4-2 1.3a9 9 0 0 0 4.2 4.2L11 8.5l4 1.5v3a2 2 0 0 1-2 2A12 12 0 0 1 1 3a2 2 0 0 1 2-2z"/></svg>
        415 903 2276
      </p>
      <p class="contact-line">
        <svg viewBox="0 0 16 16" aria-hidden="true"><path d="M1 3h14v10H1zM2 4l6 5 6-5v1L8 10 2 5z" fill-rule="evenodd"/></svg>
        info@brightpawobedience.example
      </p>
      <p class="contact-line">
        <svg viewBox="0 0 16 16" aria-hidden="true"><circle cx="8" cy="8" r="7"/></svg>
        www.brightpawobedience.example
      </p>
    </div>
  </section>

</body>
</html>
```